Marlow Sail Works President Business Card Carbon fiber catamarans

Hi.. I need a new business card design.. I am the President of a high tech yacht builder. We build Carbon Fiber go fast catamarans... Maybe we use the file I am sharing to you as the back of the card.. We need to look cool and crisp ...

Target Market(s)

Affluent People who will purchase a cool yacht

Industry/Entity Type

Custom Yacht Builder

Contact Information for Business Card

Dean Pellway , President, 731.508.2164 USA

Font styles to use
Serif

Requirements
Must have
• the clean crisp cool feel
Nice to have
• clean and crisp
Should not have
• Bold ugly

```html
<!DOCTYPE html>
<html lang="en">
<head>
<meta charset="utf-8">
<title>Marlow Sail Works – Business Card</title>
<link href="https://fonts.googleapis.com/css2?family=Play:wght@400&display=swap" rel="stylesheet">
<style>
  :root {
    --stage: #19191a;
    --carbon-dark: #111112;
    --carbon-light: #2c2c2e;
    --card-top: #3b3b3d;
    --card-bottom: #1b1b1d;
    --silver: #d9d9db;
    --silver-soft: #b8b8bb;
    --rule: #8a8a8d;
    --edge: #e8e8ea;
  }
  * { margin: 0; padding: 0; box-sizing: border-box; }
  html, body {
    width: 1200px; height: 874px; overflow: hidden;
    background: var(--stage);
    font-family: "Play", sans-serif;
    color: var(--silver);
  }
  .card {
    position: absolute;
    left: 267px;
    width: 665px; height: 380px;
    border-radius: 3px;
    overflow: hidden;
  }
  /* front */
  .card-front { top: 40px; }
  .carbon-weave {
    position: absolute; inset: 0;
    background: radial-gradient(ellipse at 45% 35%, var(--carbon-light), var(--carbon-dark) 75%);
  }
  .front-brand {
    position: absolute; left: 50%; top: 50%;
    transform: translate(-50%, -50%);
    display: flex; align-items: center; gap: 22px;
  }
  .brand-square {
    width: 64px; height: 64px;
    background: var(--silver);
  }
  .brand-name { text-transform: uppercase; line-height: 1; color: var(--silver); }
  .brand-name .primary { display: block; font-size: 60px; letter-spacing: 6px; }
  .brand-name .secondary { display: block; font-size: 26px; letter-spacing: 5px; margin-top: 6px; }

  /* back */
  .card-back {
    top: 452px;
    background: linear-gradient(180deg, var(--card-top), var(--card-bottom));
  }
  .card-back .edge-band {
    position: absolute; left: 0; right: 0; bottom: 0; height: 12px;
    background: var(--edge);
  }
  .person { position: absolute; left: 42px; top: 118px; }
  .person-name { font-size: 25px; letter-spacing: 1.5px; text-transform: uppercase; }
  .person-title { font-size: 14px; color: var(--silver-soft); margin-top: 2px; }
  .main-rule {
    position: absolute; left: 42px; top: 176px; width: 500px; height: 1px;
    background: var(--rule);
  }
  .contact-list { position: absolute; left: 42px; top: 192px; list-style: none; }
  .contact-list li {
    display: flex; align-items: center; gap: 10px;
    font-size: 18px; line-height: 25px; letter-spacing: .5px;
  }
  .contact-list svg { width: 13px; height: 13px; fill: var(--silver); flex: none; }
  .back-brand {
    position: absolute; right: 56px; top: 92px;
    text-align: center; text-transform: uppercase; color: var(--silver);
    line-height: 1.05;
  }
  .back-brand .primary { display: block; font-size: 28px; letter-spacing: 3px; }
  .back-brand .secondary { display: block; font-size: 13px; letter-spacing: 3px; margin-top: 4px; }
  .address-rule {
    position: absolute; right: 56px; top: 262px; width: 230px; height: 1px;
    background: var(--rule);
  }
  .address {
    position: absolute; right: 56px; top: 272px;
    text-align: right; font-style: normal;
    font-size: 16px; line-height: 21px; letter-spacing: .5px;
  }
</style>
</head>
<body>
  <section class="card card-front">
    <div class="carbon-weave" role="img" aria-label="Carbon fibre weave texture"></div>
    <div class="front-brand">
      <span class="brand-square"></span>
      <span class="brand-name">
        <span class="primary">Marlow</span>
        <span class="secondary">Sail Works</span>
      </span>
    </div>
  </section>

  <section class="card card-back">
    <div class="person">
      <p class="person-name">Dean Pellway</p>
      <p class="person-title">President</p>
    </div>
    <div class="main-rule"></div>
    <ul class="contact-list">
      <li>
        <svg viewBox="0 0 16 16"><path d="M3.5 1l3 3-1.6 2a9 9 0 0 0 5 5l2-1.6 3 3-1.9 2.2C7.5 15 1 8.5 1.4 2.9z"/></svg>
        731-508-2164
      </li>
      <li>
        <svg viewBox="0 0 16 16"><path d="M4 0h8a1 1 0 0 1 1 1v14a1 1 0 0 1-1 1H4a1 1 0 0 1-1-1V1a1 1 0 0 1 1-1zm1 2v10h6V2zm3 11a1 1 0 1 0 0 2 1 1 0 0 0 0-2z"/></svg>
        731-508-2190
      </li>
      <li>
        <svg viewBox="0 0 16 16"><path d="M0 3h16v1L8 9 0 4zm0 2.5l8 5 8-5V13H0z"/></svg>
        info@marlowsail.com
      </li>
    </ul>
    <div class="back-brand">
      <span class="primary">Marlow</span>
      <span class="secondary">Sail Works</span>
    </div>
    <div class="address-rule"></div>
    <address class="address">
      412 Harbor Reach Road<br>
      Newport, Rhode Island 02840<br>
      www.marlowsail.com
    </address>
    <div class="edge-band"></div>
  </section>
</body>
</html>
```